Tamarind Lodgings letterhead

We need a letterhead designed that includes the new logo that has just been designed for our business. The letterhead will need to be formatted for digital use as well as for print.

Target Market(s)

Private tenant, corporate tenants, real estate agents

Industry/Entity Type

Digital

Requirements
Must have
• ABN 87 504 912 386
PO Box 7816, Harlowe Mail Centre QLD 4790
Email: linus.pardoe@quillmail.example
Ph: 0438 617 209

```html
<!DOCTYPE html>
<html lang="en">
<head>
<meta charset="utf-8">
<title>Tamarind Lodgings Letterhead</title>
<link rel="stylesheet" href="https://fonts.googleapis.com/css2?family=Quicksand:wght@600;700&display=swap">
<style>
  :root {
    --maroon: #5b0c23;
    --brand: #7c2619;
    --ink: #8a2b1f;
    --rule: #d24a42;
    --paper: #ffffff;
  }
  * { margin: 0; padding: 0; box-sizing: border-box; }
  html, body { width: 849px; height: 1200px; overflow: hidden; background: var(--paper); }
  .letterhead {
    position: relative;
    width: 849px;
    height: 1200px;
    background: var(--paper);
    font-family: "Quicksand", sans-serif;
    border-right: 2px solid var(--rule);
    border-bottom: 2px solid var(--rule);
  }
  .side-band {
    position: absolute;
    left: 0; top: 0;
    width: 108px; height: 100%;
    background: var(--maroon);
  }
  .brand {
    position: absolute;
    left: 128px; top: 30px;
    display: flex;
    align-items: center;
    gap: 12px;
  }
  .brand-mark {
    width: 50px; height: 50px;
    background: var(--brand);
    border-radius: 6px;
  }
  .brand-name {
    font-weight: 700;
    font-size: 27px;
    line-height: 1.05;
    color: var(--brand);
    width: 150px;
  }
  .contact {
    position: absolute;
    left: 495px; top: 34px;
    list-style: none;
    font-weight: 600;
    font-size: 17px;
    line-height: 25px;
    color: var(--ink);
  }
  .header-rule {
    position: absolute;
    left: 108px; right: 0;
    top: 183px;
    height: 2px;
    background: var(--rule);
  }
</style>
</head>
<body>
  <main class="letterhead">
    <div class="side-band"></div>
    <header>
      <div class="brand">
        <div class="brand-mark"></div>
        <div class="brand-name">Tamarind Lodgings</div>
      </div>
      <ul class="contact">
        <li>ABN 87 504 912 386</li>
        <li>PO BOX 7816 , Harlowe Mail Centre</li>
        <li>QLD 4790</li>
        <li>EMAIL : linus.pardoe@quillmail.example</li>
        <li>PHONE : 0438 617 209</li>
      </ul>
    </header>
    <div class="header-rule"></div>
  </main>
</body>
</html>
```